Sales sheet for printing and embroidery apparel items - Copper Hollow Graphics

I would like a one page flyer or sales sheet that I would use as a template to send different images of apparel we produce. I have attached examples of layouts I like.
- Ideally, it would have space for 3-5 items.
- I would like it one page only - not a folding flyer.
- Our companies name is Copper Hollow Graphics.
- This will be used for many different products and markets so I don't need wording/copy. You can use wording from the 7M9 or T58 flyer.

Colors
0054AA
0677BA
7BADD7
CADEEF
E8F1F8
00AB8E
00BBA5
67D7C9
C6EFE9
E9F9F6
FFC000
F8CF3A
FAE287
FDF2CF
FEFAEE

Requirements
Must have
• Places for between 3 and 5 images of apparel (t-shirts, hats etc)

```html
<!DOCTYPE html>
<html lang="en">
<head>
<meta charset="utf-8">
<title>Copper Hollow Graphics – Custom Apparel Sales Sheet</title>
<link href="https://fonts.googleapis.com/css2?family=Bebas+Neue&family=Poppins:wght@400;500;600;700&display=swap" rel="stylesheet">
<style>
  :root{
    --blue:#0054AA;
    --blue-bright:#0a5fd0;
    --blue-deep:#0b3ea6;
    --blue-wave:#0677BA;
    --navy:#0b1a33;
    --green:#00AB8E;
    --green-soft:#00BBA5;
    --yellow:#FFC000;
    --yellow-soft:#F8CF3A;
    --white:#ffffff;
    --ink:#1b2233;
  }
  *{box-sizing:border-box;margin:0;padding:0}
  html,body{width:848px;height:1200px;overflow:hidden;background:#fff}
  .sheet{position:relative;width:848px;height:1200px;overflow:hidden;font-family:'Poppins',sans-serif;color:var(--ink);background:#fff}
  .display{font-family:'Bebas Neue',sans-serif;font-weight:400;letter-spacing:.3px}

  /* hero */
  .hero-panel{position:absolute;left:0;top:0;width:424px;height:305px;border-bottom-right-radius:44px;overflow:hidden;background:linear-gradient(160deg,var(--blue-bright),var(--blue-deep))}
  .hero-panel svg.wave{position:absolute;left:0;top:0}
  .brand-name{position:absolute;left:34px;top:20px;font-family:'Bebas Neue',sans-serif;font-size:27px;line-height:25px;color:var(--yellow)}
  .hero-title{position:absolute;left:34px;top:110px;font-size:41px;line-height:35px;color:var(--white)}
  .hero-sub{position:absolute;left:34px;top:183px;font-size:10.6px;line-height:15px;color:var(--white)}
  .features{position:absolute;left:34px;top:228px;display:flex}
  .feature{display:flex;align-items:center;margin-right:12px}
  .feature .badge{width:41px;height:41px;border-radius:50%;background:var(--yellow);display:flex;align-items:center;justify-content:center;margin-right:7px}
  .feature span{font-size:10px;line-height:12.5px;color:var(--white);text-transform:uppercase}
  .hero-photo{position:absolute;left:424px;top:0;width:424px;height:304px;border-bottom-left-radius:44px;background:radial-gradient(ellipse at 50% 45%,#e0a91c 0%,#6b5420 40%,#1a1a1a 80%)}

  /* section headings */
  .heading{position:absolute;left:0;width:848px;text-align:center;color:var(--navy)}
  .rule{position:absolute;height:2px;background:var(--yellow)}

  /* product cards */
  .card{position:absolute;top:397px;width:253px;height:255px;border-top-left-radius:42px;border-bottom-right-radius:30px;overflow:hidden}
  .card .photo{height:216px}
  .card .label{height:39px;display:flex;align-items:center;justify-content:center;color:#fff;font-weight:700;font-size:18px;letter-spacing:.5px}
  .card-tees{left:34px}
  .card-tees .photo{background:linear-gradient(135deg,#f2b61c,#3e4a2a 55%,#1f52c8)}
  .card-tees .label{background:var(--green)}
  .card-hoodies{left:297px;border-top-left-radius:0;border-bottom-right-radius:30px}
  .card-hoodies .photo{background:linear-gradient(90deg,#e4a71a,#141414 35%,#141414 70%,#1d3fb0)}
  .card-hoodies .label{background:var(--blue)}
  .card-hats{left:560px;border-top-left-radius:0;border-top-right-radius:42px}
  .card-hats .photo{background:linear-gradient(135deg,#f0b41c,#2a2a2a 50%,#cfc6ae)}
  .card-hats .label{background:var(--navy)}

  /* steps */
  .subtitle{position:absolute;left:0;top:722px;width:848px;text-align:center;font-size:11px;font-weight:500;color:var(--navy)}
  .step{position:absolute;top:762px;display:flex}
  .step .icon{width:54px;height:54px;border-radius:50%;display:flex;align-items:center;justify-content:center;flex:none;margin-right:9px}
  .step h3{font-family:'Bebas Neue',sans-serif;font-weight:400;font-size:15.5px;color:var(--navy);margin-top:4px;line-height:18px}
  .step p{font-size:7.3px;line-height:8.6px;color:var(--ink);width:135px}
  .step-ride{left:74px}.step-ride .icon{background:var(--blue)}
  .step-gear{left:312px}.step-gear .icon{background:var(--green)}.step-gear p{width:140px}
  .step-make{left:563px}.step-make .icon{background:var(--yellow)}.step-make p{width:150px}
  .arrow{position:absolute;top:788px}

  /* values */
  .values-title{top:886px;font-size:31px;line-height:27px}
  .values-copy{position:absolute;left:0;top:959px;width:848px;text-align:center;font-size:7.2px;color:var(--ink)}
  .checks{position:absolute;top:983px;display:flex;flex-direction:column;gap:3px}
  .checks li{list-style:none;display:flex;align-items:center;font-size:10.6px;font-weight:500;color:var(--navy);line-height:14px}
  .checks svg{margin-right:4px}
  .checks-left{left:141px}
  .checks-right{left:427px}
  .divider{position:absolute;left:407px;top:984px;width:1px;height:32px;background:#cfd6e0}

  /* offer band */
  .offer{position:absolute;left:0;top:1049px;width:848px;height:72px;background:var(--green);border-top-left-radius:60px 40px;border-top-right-radius:60px 40px;text-align:center}
  .offer h4{font-family:'Bebas Neue',sans-serif;font-weight:400;font-size:18px;color:var(--yellow-soft);margin-top:8px;line-height:20px}
  .offer p{font-size:12px;font-weight:600;color:var(--yellow-soft);margin-top:2px}

  /* footer */
  .footer{position:absolute;left:0;top:1118px;width:848px;height:82px;background:var(--blue)}
  .footer-hello{position:absolute;left:34px;top:14px;color:#fff}
  .footer-hello h5{font-size:12.5px;font-weight:600}
  .footer-hello small{display:block;font-size:6.4px;font-weight:600;margin-top:1px}
  .contacts{position:absolute;left:34px;top:50px;display:flex;gap:15px}
  .contact{display:flex;align-items:center;color:#fff}
  .contact .dot{width:20px;height:20px;border-radius:50%;background:#fff;display:flex;align-items:center;justify-content:center;margin-right:6px}
  .contact b{display:block;font-size:6.5px;font-weight:600}
  .contact span{font-size:6.3px}
  .footer-brand{position:absolute;left:476px;top:12px;width:56px;height:56px;background:#fff;display:flex;align-items:center;justify-content:center;text-align:center;font-family:'Bebas Neue',sans-serif;font-size:13px;line-height:12px;color:var(--blue)}
  .about{position:absolute;left:543px;top:10px;color:#fff}
  .about h6{font-family:'Bebas Neue',sans-serif;font-weight:400;font-size:18px;color:#fff;line-height:20px}
  .about p{font-size:7.7px;line-height:13.8px;width:290px}
</style>
</head>
<body>
<div class="sheet">

  <!-- hero -->
  <section class="hero-panel">
    <svg class="wave" width="424" height="305" viewBox="0 0 424 305" aria-hidden="true">
      <path d="M230 0 C250 40 320 50 360 90 C390 120 400 150 424 160 L424 0 Z" fill="var(--blue-wave)" opacity=".55"/>
      <path d="M300 0 C320 25 370 35 424 70 L424 0 Z" fill="#1a8ad0" opacity=".4"/>
    </svg>
    <div class="brand-name">Copper Hollow<br>Graphics</div>
    <h1 class="hero-title display">Custom Apparel,<br>Your Way.</h1>
    <p class="hero-sub">High-quality custom clothing made to represent<br>your brand, your team, your story.</p>
    <div class="features">
      <div class="feature">
        <div class="badge"><svg width="22" height="18" viewBox="0 0 22 18"><path d="M1 3 L6 8 L11 1 L16 8 L21 3 L19 14 L3 14 Z" fill="var(--blue-deep)"/><rect x="3" y="15" width="16" height="2.5" fill="var(--blue-deep)"/></svg></div>
        <span>Premium<br>Quality</span>
      </div>
      <div class="feature">
        <div class="badge"><svg width="22" height="20" viewBox="0 0 22 20"><path d="M7 1 L1 5 L3 9 L6 8 L6 19 L16 19 L16 8 L19 9 L21 5 L15 1 C14 3 8 3 7 1 Z" fill="var(--blue-deep)"/></svg></div>
        <span>Fully<br>Customizable</span>
      </div>
      <div class="feature">
        <div class="badge"><svg width="24" height="18" viewBox="0 0 24 18"><rect x="1" y="2" width="14" height="11" fill="var(--blue-deep)"/><path d="M15 5 L20 5 L23 9 L23 13 L15 13 Z" fill="var(--blue-deep)"/><circle cx="6" cy="14.5" r="2.5" fill="var(--blue-deep)" stroke="var(--yellow)"/><circle cx="18" cy="14.5" r="2.5" fill="var(--blue-deep)" stroke="var(--yellow)"/></svg></div>
        <span>Fast<br>Turnaround</span>
      </div>
    </div>
  </section>
  <div class="hero-photo" role="img" aria-label="Photo of custom printed hoodies, t-shirts and embroidered caps on a dark stage with yellow paint splash backdrop"></div>

  <!-- products -->
  <div class="rule" style="left:163px;top:357px;width:78px"></div>
  <h2 class="heading display" style="top:343px;font-size:30px;line-height:30px">Custom Apparel,Your Way.</h2>
  <div class="rule" style="left:608px;top:357px;width:78px"></div>

  <article class="card card-tees">
    <div class="photo" role="img" aria-label="Photo of custom printed t-shirts with vehicle graphics on a yellow and blue paint splash background"></div>
    <div class="label">T-SHIRTS</div>
  </article>
  <article class="card card-hoodies">
    <div class="photo" role="img" aria-label="Photo of yellow, black and blue printed hoodies on a dark stage"></div>
    <div class="label">HOODIES</div>
  </article>
  <article class="card card-hats">
    <div class="photo" role="img" aria-label="Photo of embroidered trucker caps stacked on dark blocks"></div>
    <div class="label">HATS</div>
  </article>

  <!-- how to order -->
  <div class="rule" style="left:183px;top:703px;width:78px"></div>
  <h2 class="heading display" style="top:689px;font-size:30px;line-height:30px">How To Start An Order</h2>
  <div class="rule" style="left:583px;top:703px;width:78px"></div>
  <p class="subtitle">Creating T-shirts is quick and easy</p>

  <div class="step step-ride">
    <div class="icon"><svg width="30" height="26" viewBox="0 0 30 26"><path d="M4 12 L7 6 L17 6 L20 12 Z" fill="#fff"/><rect x="2" y="12" width="20" height="8" rx="2" fill="#fff"/><rect x="4" y="20" width="4" height="3" fill="#fff"/><rect x="16" y="20" width="4" height="3" fill="#fff"/><circle cx="6" cy="16" r="1.5" fill="var(--blue)"/><circle cx="18" cy="16" r="1.5" fill="var(--blue)"/><circle cx="22" cy="6" r="4.5" fill="var(--blue)" stroke="#fff" stroke-width="2"/><path d="M25 9 L29 13" stroke="#fff" stroke-width="2.5"/></svg></div>
    <div><h3>Choose Your Ride</h3><p>Send us a picture, or let us know the make and model of the vehicle you would like featured on your apparel.</p></div>
  </div>
  <svg class="arrow" style="left:272px" width="32" height="10" viewBox="0 0 32 10"><path d="M0 5 L30 5 M25 1 L30 5 L25 9" stroke="var(--green)" stroke-width="1.2" fill="none"/></svg>
  <div class="step step-gear">
    <div class="icon"><svg width="30" height="26" viewBox="0 0 30 26"><rect x="2" y="2" width="24" height="18" rx="2" fill="none" stroke="#fff" stroke-width="2"/><line x1="2" y1="6" x2="26" y2="6" stroke="#fff" stroke-width="1.5"/><path d="M10 9 L7 11 L8 13 L10 12.5 L10 18 L17 18 L17 12.5 L19 13 L20 11 L17 9 Z" fill="#fff"/><path d="M20 16 L28 20 L24 21 L26 25 L24 25.5 L22 22 L19 24 Z" fill="#fff"/></svg></div>
    <div><h3>Pick Your Gear</h3><p>We will help you choose your t-shirts, sweatshirts or other apparel items and determine sizes and quantities.</p></div>
  </div>
  <svg class="arrow" style="left:518px" width="32" height="10" viewBox="0 0 32 10"><path d="M0 5 L30 5 M25 1 L30 5 L25 9" stroke="var(--yellow)" stroke-width="1.2" fill="none"/></svg>
  <div class="step step-make">
    <div class="icon"><svg width="32" height="28" viewBox="0 0 32 28"><path d="M10 2 L2 7 L5 13 L8 12 L8 27 L24 27 L24 12 L27 13 L30 7 L22 2 C20 5 12 5 10 2 Z" fill="#111"/><path d="M16 11 L17.5 15 L21.5 15 L18.3 17.4 L19.5 21.3 L16 19 L12.5 21.3 L13.7 17.4 L10.5 15 L14.5 15 Z" fill="var(--yellow)"/></svg></div>
    <div><h3>We Customize</h3><p>We make the magic happen and our team of expert artists will design your shirts and get a proof out to you. Upon order approval your order will go into production</p></div>
  </div>

  <!-- values -->
  <div class="rule" style="left:162px;top:911px;width:77px"></div>
  <h2 class="heading display values-title">We Are Catholic And Love<br>To Help Catholic Movements.</h2>
  <div class="rule" style="left:627px;top:911px;width:77px"></div>
  <p class="values-copy">We promise good quality shirts that look the way you want. We promise quick delivery, and we take care of royalty fees.</p>
  <ul class="checks checks-left">
    <li><svg width="9" height="9" viewBox="0 0 10 10"><circle cx="5" cy="5" r="5" fill="var(--blue)"/><path d="M2.6 5.2 L4.3 6.8 L7.4 3.4" stroke="#fff" stroke-width="1.3" fill="none"/></svg>We’re Catholic And Believe In Catholic Values.</li>
    <li><svg width="9" height="9" viewBox="0 0 10 10"><circle cx="5" cy="5" r="5" fill="var(--blue)"/><path d="M2.6 5.2 L4.3 6.8 L7.4 3.4" stroke="#fff" stroke-width="1.3" fill="none"/></svg>We Promise To Provide The Shirt You Want</li>
  </ul>
  <div class="divider"></div>
  <ul class="checks checks-right">
    <li><svg width="9" height="9" viewBox="0 0 10 10"><circle cx="5" cy="5" r="5" fill="var(--blue)"/><path d="M2.6 5.2 L4.3 6.8 L7.4 3.4" stroke="#fff" stroke-width="1.3" fill="none"/></svg>We Work With Multiple Chapters Of The Movement</li>
    <li><svg width="9" height="9" viewBox="0 0 10 10"><circle cx="5" cy="5" r="5" fill="var(--blue)"/><path d="M2.6 5.2 L4.3 6.8 L7.4 3.4" stroke="#fff" stroke-width="1.3" fill="none"/></svg>We Can Send Examples Of Shirts We’ve Printed.</li>
  </ul>

  <!-- offer -->
  <section class="offer">
    <h4>We Offer:</h4>
    <p>Art Design • Free Shipping • We Pay ALL Royalties to the Movement Many Options of Shirt Styles and Colors</p>
  </section>

  <!-- footer -->
  <footer class="footer">
    <div class="footer-hello">
      <h5>We'd Love To Work With You!</h5>
      <small>Contact Marcus Delane To Start Your Next Shirt Order Today.</small>
    </div>
    <div class="contacts">
      <div class="contact">
        <div class="dot"><svg width="11" height="11" viewBox="0 0 12 12"><path d="M3 1 L5 3.5 L4 5 C5 7 6 8 7.5 8.5 L9 7.5 L11 9.5 L9.5 11 C5 11 1 7 1 2.5 Z" fill="var(--blue)"/></svg></div>
        <div><b>Phone</b><span>555-014-2273</span></div>
      </div>
      <div class="contact">
        <div class="dot"><svg width="11" height="9" viewBox="0 0 12 9"><rect x=".5" y=".5" width="11" height="8" rx="1" fill="none" stroke="var(--blue)"/><path d="M1 1 L6 5 L11 1" stroke="var(--blue)" fill="none"/></svg></div>
        <div><b>Email</b><span>Marcus@Chgtshirts.Com</span></div>
      </div>
      <div class="contact">
        <div class="dot"><svg width="11" height="11" viewBox="0 0 12 12"><circle cx="6" cy="6" r="5" fill="none" stroke="var(--blue)"/><ellipse cx="6" cy="6" rx="2.2" ry="5" fill="none" stroke="var(--blue)"/><line x1="1" y1="6" x2="11" y2="6" stroke="var(--blue)"/></svg></div>
        <div><b>Website</b><span>Chgtshirts.Com</span></div>
      </div>
    </div>
    <div class="footer-brand">Copper<br>Hollow<br>Graphics</div>
    <div class="about">
      <h6>About Us</h6>
      <p>Copper Hollow Graphics Is A Second-Generation Screen Printing Company In Alder Falls, VA. For Over 45 Years, We’ve Specialized In High-Quality Custom Apparel And Merchandise.</p>
    </div>
  </footer>

</div>
</body>
</html>
```